KAJU Freightways #ALLKAJU Business Cards & Letterhead

I am looking to business cards designed for our organization. We are currently undergoing a small re-branding that is taking place. Our organization is called KAJU Freightways and we are headquartered in Phoenix, AZ. We primarily provide transportation and logistics services to the Marlow Parcel Bureau who is our largest customer. I would like to see a design that incorporates name, title, contact info, website, and address (this will be different depending on the employee). I would also like to see some color on the business card using our logo colors or a variation. I would like our logo on the back of the business card with the website displayed. The final design should communicate that we are a next generation transportation operate that focuses on being driver-first, customer-centric, innovative, and sustainable.We would also like our #ALLKAJU catch phrase incorporated as well.

Target Market(s)

Transportation & Logistics

Industry/Entity Type

Trucking Company

Contact Information for Business Card

-First and Last Name
-Position Title
-Contact Phone
-Contact Email
-Physical Address

Font styles to use
Serif

Colors

Designer to choose colors to be used in the design.

Requirements
Must have
• -KAJU logo prominently displayed
• -#ALLKAJU catch phrase used
• -Some amount of color, design gradient, etc.
• -Logo on the back with website listed (https://www.kajufreightco.example)

```html
<!DOCTYPE html>
<html lang="en">
<head>
<meta charset="utf-8">
<title>KAJU Freightways Business Card</title>
<link href="https://fonts.googleapis.com/css2?family=Merriweather:wght@400;700;900&display=swap" rel="stylesheet">
<style>
  :root {
    --bg: #9a9a9a;
    --teal-light: #0b5a66;
    --teal-dark: #03353f;
    --ink: #0f3f4a;
    --green: #6fbe3e;
    --grey-text: #5d6468;
    --silver: #d4d6d8;
    --white: #ffffff;
  }
  * { margin: 0; padding: 0; box-sizing: border-box; }
  html, body { width: 1200px; height: 960px; overflow: hidden; }
  body {
    background: var(--bg);
    font-family: "Merriweather", serif;
    position: relative;
  }
  .card {
    position: absolute;
    width: 700px;
    height: 400px;
    border-radius: 26px;
    overflow: hidden;
  }
  .card-back {
    left: 60px;
    top: 50px;
    background: linear-gradient(135deg, var(--teal-light) 0%, var(--teal-dark) 100%);
  }
  .card-front {
    left: 440px;
    top: 510px;
    background: var(--white);
  }
  .wordmark-ring {
    position: absolute;
    border-radius: 50%;
    display: flex;
    align-items: center;
    justify-content: center;
  }
  .card-back .wordmark-ring {
    width: 230px; height: 230px;
    left: 235px; top: 40px;
    border: 6px solid var(--silver);
  }
  .card-front .wordmark-ring {
    width: 200px; height: 200px;
    left: 100px; top: 95px;
    border: 7px solid var(--green);
  }
  .wordmark {
    font-weight: 900;
    letter-spacing: 1px;
  }
  .card-back .wordmark { color: var(--silver); font-size: 52px; }
  .card-front .wordmark { color: var(--ink); font-size: 44px; }
  .back-tagline {
    position: absolute;
    left: 0; width: 700px; top: 292px;
    text-align: center;
    color: var(--green);
    font-weight: 700;
    font-size: 22px;
    letter-spacing: 3px;
  }
  .back-website {
    position: absolute;
    left: 0; width: 700px; top: 335px;
    text-align: center;
    color: var(--silver);
    font-size: 15px;
    letter-spacing: 1px;
  }
  .swoosh { position: absolute; left: 0; top: 0; }
  .divider {
    position: absolute;
    left: 355px; top: 80px;
    width: 1px; height: 185px;
    background: linear-gradient(to bottom, rgba(0,0,0,0), #b8bcbe 40%, rgba(0,0,0,0));
  }
  .details {
    position: absolute;
    left: 380px; top: 62px;
    color: var(--grey-text);
  }
  .person-name {
    font-weight: 700;
    font-size: 21px;
    color: var(--ink);
    letter-spacing: 0.5px;
    text-transform: uppercase;
  }
  .person-title {
    font-size: 14px;
    color: var(--green);
    margin: 2px 0 10px;
  }
  .address { font-size: 12.5px; line-height: 19px; margin-bottom: 10px; }
  .contact-list { list-style: none; font-size: 12.5px; line-height: 21px; }
  .contact-list li { display: flex; align-items: center; gap: 9px; }
  .contact-list svg { width: 12px; height: 12px; fill: var(--ink); flex: none; }
</style>
</head>
<body>

<section class="card card-back" aria-label="Business card back">
  <div class="wordmark-ring"><span class="wordmark">KAJU</span></div>
  <p class="back-tagline">#ALLKAJU</p>
  <p class="back-website">www.kajufreightco.example</p>
</section>

<section class="card card-front" aria-label="Business card front">
  <svg class="swoosh" width="700" height="400" viewBox="0 0 700 400" aria-hidden="true">
    <defs>
      <linearGradient id="tealBand" x1="0" y1="0" x2="1" y2="1">
        <stop offset="0" stop-color="#0b5a66"/>
        <stop offset="1" stop-color="#03353f"/>
      </linearGradient>
    </defs>
    <path d="M0 352 C 250 340, 500 318, 700 278 L700 400 L0 400 Z" fill="var(--green)"/>
    <path d="M0 368 C 250 355, 500 333, 700 294 L700 400 L0 400 Z" fill="url(#tealBand)"/>
  </svg>

  <div class="wordmark-ring"><span class="wordmark">KAJU</span></div>
  <div class="divider"></div>

  <div class="details">
    <p class="person-name">Daniel Harper</p>
    <p class="person-title">President</p>
    <p class="address">412 Saguaro Ridge Road<br>Phoenix, Arizona 85034</p>
    <ul class="contact-list">
      <li><svg viewBox="0 0 24 24"><path d="M6.6 10.8a15 15 0 0 0 6.6 6.6l2.2-2.2a1 1 0 0 1 1-.25 11.4 11.4 0 0 0 3.6.57 1 1 0 0 1 1 1V20a1 1 0 0 1-1 1A17 17 0 0 1 3 4a1 1 0 0 1 1-1h3.5a1 1 0 0 1 1 1c0 1.25.2 2.45.57 3.57a1 1 0 0 1-.25 1z"/></svg>480-555-0172</li>
      <li><svg viewBox="0 0 24 24"><path d="M2 5h20v14H2z M4 7v.4l8 5 8-5V7l-8 5z" fill-rule="evenodd"/></svg>dharper@kajufreightco.example</li>
      <li><svg viewBox="0 0 24 24"><circle cx="12" cy="12" r="10"/></svg>www.kajufreightco.example</li>
    </ul>
  </div>
</section>

</body>
</html>
```